New App: 4 Page Design - Updated Brief

We need an indicative design for our new app 'Kit Runner', a delivery service for tools and hardware in Sydney, Australia.

Imagine a service which copies the blue print of Zolvo Meals, but for tools and Hardware. Where builders and tradespeople are stuck on-site at work and need a tool to be delivered to them on-site, same day. They can jump onto this app and in-put their address, then select an item from the catalogue and confirm the order. Once the order has been collected and due for delivery a map will show the location of the delivery driver.

We'd like 4 pages designed.

1st page) Loading page, similar to but not the same as the ZolvoMeals example attached.

2nd page) Home page - featuring the logo and some icons which direct users around the website. (Please see link to design example: https://www.zolvomeals.example/au?ref_id=a1b2c3d4-e5f6-47a8-9b0c-d1e2f3a4b5c6 )

3rd page) A page which depicts the catalogue of tools and hardware (showing generic tools available (Please see link to design example https://www.trellmart.example/products/building-hardware).

4th page) We'd like a page which shows a map, tracking the delivery, from the hardware store, to the location of the purchaser, exactly like any typical zolvo delivery service.

Please see the below website for design guidance and ideas

https://www.trellmart.example/?src=ab.cd&ref=Xy7QpLm3Rt9Vw2KsNh4Bf8JdZc6GaT1YeUo5Mi0Wq3ErPx7Ls2Dn9Hv4Ck8Fj6Bg1Az5Tm3Ry0Qu7Wp2Xo4Zi9Ke6Jl8Nb3Vc1Sd5Ph7Mf_abc

Target Market(s)

Construction industry, tradespeople

Industry/Entity Type

Construction and Tradesmen

Colors

Designer to choose colors to be used in the design.

Requirements
Must have
• Desired Colour schemes: up to the designer but no bright colours
Nice to have
• An icon bar at the bottom of the page that directs you to the various pages on the app. Example shown in the attachments
Should not have
• An exact copy of the Zolvo App

```html
<!DOCTYPE html>
<html lang="en">
<head>
<meta charset="utf-8">
<title>Kit Runner – Home</title>
<link href="https://fonts.googleapis.com/css2?family=Poppins:wght@400;500;600;700&display=swap" rel="stylesheet">
<style>
:root{
  --accent:#D4862F;
  --accent-deep:#B8721F;
  --accent-soft:#DDA35F;
  --bg:#F2F1F6;
  --card:#F3F2F7;
  --border:#E4E3EA;
  --ink:#2E2E2E;
  --ink-soft:#444;
  --muted:#8C8C92;
  --tab-idle:#A4A4AA;
  --white:#FFFFFF;
  --dot:#D3D2D8;
}
*{margin:0;padding:0;box-sizing:border-box}
html,body{width:1200px;height:2431px;overflow:hidden;background:var(--bg)}
body{font-family:'Poppins',sans-serif;color:var(--ink);position:relative}
.abs{position:absolute}
.status-time{left:165px;top:62px;font-size:44px;font-weight:500;letter-spacing:1px}
.status-icons{right:110px;top:70px}
.header{left:0;top:0;width:1200px;height:532px;background:var(--bg);box-shadow:0 8px 18px rgba(0,0,0,.05)}
.deliver-label{left:57px;top:205px;font-size:33px;color:var(--muted)}
.deliver-address{left:57px;top:265px;font-size:34px;font-weight:600;color:var(--ink-soft);display:flex;align-items:center;gap:24px}
.orders-shortcut{left:1078px;top:218px}
.search{left:59px;top:353px;width:1077px;height:122px;border:2px solid var(--border);border-radius:16px;display:flex;align-items:center;padding-left:40px;gap:50px}
.search span{font-size:34px;color:var(--muted)}
.section-title{left:57px;font-size:39px;font-weight:600;color:var(--ink-soft)}
.deal-banner{left:59px;top:633px;width:1077px;height:402px;border-radius:24px;overflow:hidden;box-shadow:0 8px 20px rgba(0,0,0,.08);
  background:linear-gradient(90deg,var(--accent-deep) 0%,var(--accent) 35%,#D9B586 65%,#D4CCC0 100%)}
.deal-banner h2{position:absolute;left:62px;top:68px;color:var(--white);font-size:50px;font-weight:600;line-height:82px;letter-spacing:.5px}
.shop-btn{position:absolute;left:61px;top:264px;width:315px;height:80px;border-radius:40px;background:var(--white);display:flex;align-items:center;justify-content:center;font-size:33px;color:var(--ink-soft)}
.pager{left:59px;top:1105px;display:flex;gap:40px;align-items:center}
.pager i{display:block;width:22px;height:22px;border-radius:50%;background:var(--dot)}
.pager i.active{width:55px;border-radius:11px;background:var(--accent)}
.category{width:200px;text-align:center}
.category .tile{width:200px;height:200px;border:2px solid var(--border);border-radius:22px;background:var(--card);display:flex;align-items:center;justify-content:center}
.category p{margin-top:38px;font-size:34px;color:var(--ink-soft);white-space:nowrap;margin-left:-40px;margin-right:-40px}
.brand-card{top:2035px;width:430px;height:200px;background:var(--white);border-radius:20px;box-shadow:0 4px 14px rgba(0,0,0,.05);display:flex;align-items:center;justify-content:center;padding-bottom:10px}
.brand-name{font-size:56px;font-weight:700;color:#1A1A1A;display:flex;align-items:center;gap:14px}
.tab-bar{left:0;top:2190px;width:1200px;height:241px;background:var(--bg);box-shadow:0 -6px 16px rgba(0,0,0,.05)}
.tab{top:56px;width:200px;text-align:center;font-size:34px;line-height:48px;color:var(--tab-idle)}
.tab-icon{height:70px;display:flex;align-items:flex-end;justify-content:center;margin-bottom:20px}
.tab.active{color:var(--ink);font-weight:600}
</style>
</head>
<body>

<div class="abs header"></div>

<div class="abs status-time">9:41</div>
<svg class="abs status-icons" width="200" height="40" viewBox="0 0 200 40" aria-hidden="true">
  <rect x="0" y="26" width="8" height="10" rx="2" fill="#111"/>
  <rect x="12" y="20" width="8" height="16" rx="2" fill="#111"/>
  <rect x="24" y="12" width="8" height="24" rx="2" fill="#111"/>
  <rect x="36" y="4" width="8" height="32" rx="2" fill="#111"/>
  <path d="M62 14a34 34 0 0 1 46 0l-4 4a28 28 0 0 0-38 0z M70 22a22 22 0 0 1 30 0l-4 4a16 16 0 0 0-22 0z M78 30a10 10 0 0 1 14 0l-7 7z" fill="#111"/>
  <rect x="126" y="6" width="62" height="30" rx="8" fill="none" stroke="#111" stroke-width="4"/>
  <rect x="132" y="12" width="50" height="18" rx="4" fill="#111"/>
  <rect x="192" y="16" width="5" height="10" rx="2" fill="#111"/>
</svg>

<div class="abs deliver-label">Deliver to :</div>
<div class="abs deliver-address">42 Harlow Lane, Sydney
  <svg width="30" height="20" viewBox="0 0 30 20" aria-hidden="true"><path d="M3 4l12 11 12-11" fill="none" stroke="var(--accent)" stroke-width="4" stroke-linecap="round" stroke-linejoin="round"/></svg>
</div>
<svg class="abs orders-shortcut" width="58" height="74" viewBox="0 0 58 74" aria-label="Order list">
  <rect x="0" y="8" width="58" height="66" rx="8" fill="#3A3A3A"/>
  <rect x="16" y="0" width="26" height="14" rx="4" fill="#3A3A3A" stroke="var(--bg)" stroke-width="3"/>
  <rect x="12" y="28" width="26" height="5" rx="2" fill="var(--bg)"/><rect x="42" y="28" width="5" height="5" fill="var(--bg)"/>
  <rect x="12" y="40" width="26" height="5" rx="2" fill="var(--bg)"/><rect x="42" y="40" width="5" height="5" fill="var(--bg)"/>
  <rect x="12" y="52" width="26" height="5" rx="2" fill="var(--bg)"/><rect x="42" y="52" width="5" height="5" fill="var(--bg)"/>
</svg>

<div class="abs search">
  <svg width="52" height="52" viewBox="0 0 52 52" aria-hidden="true"><circle cx="22" cy="22" r="18" fill="none" stroke="#222" stroke-width="4"/><path d="M35 35l13 13" stroke="#222" stroke-width="4" stroke-linecap="round"/></svg>
  <span>What can we help you find?</span>
</div>

<div class="abs section-title" style="top:535px">Deals of the week</div>

<div class="abs deal-banner" role="img" aria-label="Photo of a bright modern kitchen with appliances and bar stools, tinted amber">
  <h2>HOME APPLIENCES<br>START FROM $99</h2>
  <div class="shop-btn">Shop Now</div>
</div>

<div class="abs pager"><i class="active"></i><i></i><i></i><i></i></div>

<div class="abs section-title" style="top:1177px">Categories</div>

<div class="abs category" style="left:78px;top:1270px">
  <div class="tile"><svg width="100" height="100" viewBox="0 0 100 100" aria-hidden="true">
    <path d="M12 86L60 38" stroke="var(--accent)" stroke-width="12" stroke-linecap="round"/>
    <circle cx="70" cy="28" r="20" fill="var(--accent)"/><path d="M72 10l14 14-10 4-8-8z" fill="var(--card)"/>
    <path d="M18 12l10-4 52 60" stroke="var(--accent)" stroke-width="12" stroke-linecap="round" fill="none"/>
    <rect x="68" y="68" width="20" height="20" rx="4" transform="rotate(45 78 78)" fill="var(--accent)"/></svg></div>
  <p>Tools</p>
</div>
<div class="abs category" style="left:358px;top:1270px">
  <div class="tile"><svg width="110" height="110" viewBox="0 0 110 110" aria-hidden="true">
    <path d="M56 92C40 92 20 84 8 68c18-6 36 0 48 24z" fill="var(--accent)"/>
    <path d="M56 92c2-18 20-28 40-24-10 16-24 24-40 24z" fill="var(--accent)"/>
    <path d="M56 92V66" stroke="var(--accent)" stroke-width="5"/>
    <path d="M58 30l20-20 22 22-20 20z" fill="var(--accent)"/>
    <circle cx="86" cy="18" r="10" fill="none" stroke="var(--accent)" stroke-width="5"/>
    <path d="M58 40l-6 8M64 46l-4 8" stroke="var(--accent)" stroke-width="4" stroke-linecap="round"/></svg></div>
  <p>Garden</p>
</div>
<div class="abs category" style="left:638px;top:1270px">
  <div class="tile"><svg width="110" height="110" viewBox="0 0 110 110" aria-hidden="true">
    <rect x="20" y="14" width="20" height="8" fill="var(--accent)"/><path d="M10 32q0-10 20-10t20 10z" fill="var(--accent)"/>
    <rect x="8" y="42" width="46" height="56" fill="var(--accent)"/><rect x="16" y="56" width="30" height="30" fill="var(--card)"/><rect x="21" y="61" width="20" height="20" fill="var(--accent)"/>
    <rect x="58" y="50" width="46" height="48" fill="var(--accent)"/><rect x="64" y="58" width="34" height="6" fill="var(--card)"/><rect x="64" y="70" width="8" height="22" fill="var(--card)"/></svg></div>
  <p>Kitchen</p>
</div>
<div class="abs category" style="left:918px;top:1270px">
  <div class="tile"><svg width="110" height="110" viewBox="0 0 110 110" aria-hidden="true">
    <rect x="6" y="10" width="86" height="28" rx="4" fill="var(--accent)"/>
    <path d="M92 24h8v24H50v12" fill="none" stroke="var(--accent)" stroke-width="5"/>
    <rect x="41" y="60" width="18" height="42" rx="3" fill="var(--accent)"/></svg></div>
  <p>Paint</p>
</div>

<div class="abs category" style="left:78px;top:1581px">
  <div class="tile"><svg width="100" height="100" viewBox="0 0 100 100" aria-hidden="true">
    <path d="M50 8L92 38v44a10 10 0 0 1-10 10H18a10 10 0 0 1-10-10V38z" fill="var(--accent)" stroke="var(--accent)" stroke-width="4" stroke-linejoin="round"/>
    <path d="M30 56a28 28 0 0 1 40 0M38 64a16 16 0 0 1 24 0" fill="none" stroke="var(--card)" stroke-width="6" stroke-linecap="round"/><circle cx="50" cy="74" r="5" fill="var(--card)"/></svg></div>
  <p>Smart Home</p>
</div>
<div class="abs category" style="left:358px;top:1581px">
  <div class="tile"><svg width="110" height="110" viewBox="0 0 110 110" aria-hidden="true">
    <path d="M92 6l8 4-18 38-10-4z" fill="var(--accent)"/>
    <path d="M66 40l24 10c-6 22-20 42-40 50-10-2-26-8-34-16 18-2 32-12 36-22-8 4-16 4-20 2 14-6 26-16 34-24z" fill="var(--accent)"/>
    <circle cx="14" cy="26" r="7" fill="var(--accent)"/><circle cx="30" cy="38" r="9" fill="var(--accent)"/><circle cx="26" cy="14" r="4" fill="var(--accent)"/></svg></div>
  <p>Cleaning</p>
</div>
<div class="abs category" style="left:638px;top:1581px">
  <div class="tile"><svg width="110" height="110" viewBox="0 0 110 110" aria-hidden="true">
    <path d="M22 28q0-10 12-10h42q12 0 12 10v16H22z" fill="var(--accent)"/>
    <rect x="4" y="40" width="22" height="38" rx="11" fill="var(--accent)"/><rect x="84" y="40" width="22" height="38" rx="11" fill="var(--accent)"/>
    <rect x="20" y="54" width="70" height="28" rx="4" fill="var(--accent)"/>
    <rect x="24" y="82" width="10" height="10" fill="var(--accent)"/><rect x="76" y="82" width="10" height="10" fill="var(--accent)"/></svg></div>
  <p>Living Room</p>
</div>
<div class="abs category" style="left:918px;top:1581px">
  <div class="tile"><svg width="110" height="30" viewBox="0 0 110 30" aria-hidden="true">
    <circle cx="15" cy="15" r="12" fill="var(--accent)"/><circle cx="55" cy="15" r="12" fill="var(--accent)"/><circle cx="95" cy="15" r="12" fill="var(--accent)"/></svg></div>
  <p>See All</p>
</div>

<div class="abs section-title" style="top:1920px">Leading Brands</div>

<div class="abs brand-card" style="left:59px"><span class="brand-name">Vextra</span></div>
<div class="abs brand-card" style="left:554px"><span class="brand-name">Halberd's</span></div>
<div class="abs brand-card" style="left:1050px;justify-content:flex-start;padding-left:100px"><span class="brand-name"><svg width="44" height="44" viewBox="0 0 44 44" aria-hidden="true"><circle cx="22" cy="22" r="19" fill="none" stroke="#1A1A1A" stroke-width="4"/></svg>Norvik</span></div>

<nav class="abs tab-bar">
  <div class="abs tab active" style="left:67px">
    <div class="tab-icon"><svg width="70" height="62" viewBox="0 0 70 62" aria-hidden="true"><path d="M35 2L2 30h10v30h18V42h10v18h18V30h10z" fill="var(--accent)"/></svg></div>Home</div>
  <div class="abs tab" style="left:346px">
    <div class="tab-icon"><svg width="70" height="66" viewBox="0 0 70 66" aria-hidden="true"><path d="M4 4h50v34a20 20 0 0 0-8 26H4z" fill="var(--tab-idle)"/><rect x="12" y="14" width="34" height="5" fill="var(--bg)"/><rect x="12" y="26" width="26" height="5" fill="var(--bg)"/><circle cx="54" cy="50" r="14" fill="var(--tab-idle)"/><path d="M47 50l5 5 9-9" fill="none" stroke="var(--bg)" stroke-width="4"/></svg></div>Orders</div>
  <div class="abs tab" style="left:620px">
    <div class="tab-icon"><svg width="70" height="66" viewBox="0 0 70 66" aria-hidden="true"><path d="M2 4h12l8 36h38l8-28H18" fill="none" stroke="var(--tab-idle)" stroke-width="6" stroke-linejoin="round"/><path d="M18 12h50l-8 28H22z" fill="var(--tab-idle)"/><circle cx="26" cy="56" r="6" fill="var(--tab-idle)"/><circle cx="56" cy="56" r="6" fill="var(--tab-idle)"/></svg></div>Carts</div>
  <div class="abs tab" style="left:909px">
    <div class="tab-icon"><svg width="60" height="62" viewBox="0 0 60 62" aria-hidden="true"><circle cx="30" cy="16" r="14" fill="var(--tab-idle)"/><path d="M2 60c0-16 12-26 28-26s28 10 28 26z" fill="var(--tab-idle)"/></svg></div>Account</div>
</nav>

</body>
</html>
```